Security based company delivering High Risk Training to Law Enforcement Agencies Worldwide.

We need a Web design for a company doing business in Washington D.C. We deliver High Risk Training to Law Enforcement Agencies throughout the world. Our focus is on Improvised Explosive Devices. We train Bomb Technicians and First Responders in all aspects relating to bombings and criminal incidents globally.
Updates

Reason: We have uploaded our logo. Thank you.

Target Market(s)

Military and Law Enforcement Personnel from around the world.

Industry/Entity Type

Business

Requirements
Should not have
• Do not include cartoon like characters.

```html
<!DOCTYPE html>
<html lang="en">
<head>
<meta charset="utf-8">
<title>Vantrex International – High Risk Training</title>
<link rel="stylesheet" href="https://fonts.googleapis.com/css2?family=Oswald:wght@400;500;600;700&family=Open+Sans:wght@400;600;700&display=swap">
<style>
:root{
  --black:#0d0d0d;
  --charcoal:#1f1f1f;
  --band:#3a3a3a;
  --band-dark:#2b2b2b;
  --grey:#d9d9d9;
  --grey-mid:#9a9a9a;
  --panel:#cfcfcf;
  --white:#ffffff;
  --text:#2a2a2a;
  --red:#b3191c;
  --blue:#1f5fa8;
  --nav:#e6e6e6;
}
*{box-sizing:border-box;margin:0;padding:0}
html,body{width:851px;height:1200px;overflow:hidden}
body{font-family:"Open Sans",Arial,sans-serif;color:var(--text);background:var(--white);position:relative}
.wrap{position:absolute;left:60px;width:731px}

/* header */
.site-header{position:absolute;top:0;left:0;width:851px;height:96px;background:linear-gradient(#1b1b1b,var(--black))}
.brand{position:absolute;left:60px;top:22px;display:flex;align-items:center;gap:10px}
.brand-mark{width:44px;height:44px;border-radius:50%;background:var(--red)}
.brand-name{font-family:"Oswald",sans-serif;font-weight:700;color:var(--white);font-size:28px;line-height:1;letter-spacing:1px}
.brand-name small{display:block;font-size:13px;letter-spacing:3px;margin-top:3px}
.contact-line{position:absolute;right:60px;top:10px;display:flex;gap:16px;font-size:10px;color:#ccc}
.contact-line span{display:flex;align-items:center;gap:4px}
.tagline{position:absolute;right:60px;top:34px;font-size:11px;font-weight:600;color:var(--white)}
.social{display:flex;gap:5px}
.social span{width:16px;height:16px;border:1px solid #888;background:#222;display:block}
.site-header .social{position:absolute;right:60px;top:56px}

/* nav */
.main-nav{position:absolute;top:96px;left:0;width:851px;height:28px;background:var(--nav);border-bottom:1px solid #bbb}
.main-nav ul{position:absolute;left:60px;top:0;display:flex;list-style:none;height:28px}
.main-nav li{font-family:"Oswald",sans-serif;font-size:11px;color:#333;padding:0 12px;line-height:28px;border-right:1px solid #c4c4c4}
.main-nav li.active{background:var(--white);color:var(--red)}
.dropdown{position:absolute;left:129px;top:124px;width:96px;background:var(--white);border:1px solid #ccc;font-size:9px;z-index:3}
.dropdown div{padding:4px 8px;border-bottom:1px solid #e3e3e3}
.dropdown div:last-child{color:var(--red)}
.search{position:absolute;right:60px;top:5px;width:130px;height:18px;background:var(--white);border:1px solid #bbb;font-size:9px;color:#999;padding:2px 6px}

/* hero */
.hero{position:absolute;top:124px;left:0;width:851px;height:364px;background:linear-gradient(160deg,#c9c3b8 0%,#a69c8a 40%,#6f6a5e 70%,#3e3d38 100%)}
.hero-caption{position:absolute;left:0;right:0;top:210px;text-align:center}
.hero-caption h1{display:inline-block;font-family:"Oswald",sans-serif;font-weight:500;font-size:22px;letter-spacing:1px;color:var(--white);background:rgba(30,30,30,.75);padding:3px 22px}
.hero-caption p{margin:8px auto 0;display:inline-block;font-size:13px;color:var(--white);background:rgba(30,30,30,.6);padding:3px 18px}
.hero-arrow{position:absolute;top:165px;width:32px;height:32px;border-radius:50%;background:rgba(40,40,40,.7)}
.hero-arrow.prev{left:60px}.hero-arrow.next{right:60px}

/* section band */
.band{position:absolute;left:0;width:851px;height:72px;background:linear-gradient(var(--band),var(--band-dark));display:flex;align-items:center;justify-content:center;gap:12px}
.band h2{font-family:"Oswald",sans-serif;font-weight:600;font-size:34px;color:var(--white);letter-spacing:1px}
.band-dot{width:22px;height:22px;border-radius:50%;background:var(--red);border:3px solid var(--blue)}

/* about */
.about{top:572px;height:170px}
.about h3{font-size:14px;font-weight:700;color:#111;margin-bottom:8px}
.about p{font-size:11px;line-height:1.35;margin-bottom:8px;width:330px}
.video{position:absolute;left:400px;top:0;width:331px;height:150px;background:linear-gradient(135deg,#8f8878,#5d5a50 55%,#3a3a36)}
.video-title{position:absolute;left:0;top:0;right:0;height:18px;background:rgba(0,0,0,.55);font-size:9px;color:#fff;padding:3px 6px}
.play{position:absolute;left:145px;top:55px;width:42px;height:30px;border-radius:6px;background:rgba(20,20,20,.8)}
.watch-btn{position:absolute;left:0;top:168px;width:731px;height:22px;background:linear-gradient(#4a4a4a,#2b2b2b);color:var(--white);font-size:11px;font-weight:600;display:flex;align-items:center;justify-content:flex-end;padding-right:330px}

/* services */
.services-bg{position:absolute;top:837px;left:0;width:851px;height:166px;background:linear-gradient(#5a5a5a,#cfcfcf)}
.cards{position:absolute;left:60px;top:850px;width:731px;display:flex;justify-content:space-between}
.card{width:170px;height:130px;background:var(--white);border:1px solid #bbb;box-shadow:0 3px 6px rgba(0,0,0,.35)}
.card-img{height:96px;margin:4px 4px 0;background:linear-gradient(135deg,#8a7f6c,#4d4a42)}
.card.alt .card-img{background:linear-gradient(135deg,#7a6a5a,#3e362f)}
.card h4{font-family:"Open Sans",sans-serif;font-weight:700;font-size:13px;text-align:center;line-height:28px;color:#111}
.card.hover{background:#bdbdbd}
.card.hover .card-img{position:relative;background:#9c9c9c}
.card-icons{position:absolute;inset:0;display:flex;align-items:center;justify-content:center;gap:10px}
.card-icons span{width:28px;height:28px;border-radius:50%;border:2px solid #fff;display:flex;align-items:center;justify-content:center}

/* footer */
.site-footer{position:absolute;top:1003px;left:0;width:851px;height:197px;background:var(--charcoal);color:#bbb}
.footer-cols{position:absolute;left:60px;top:26px;display:flex;gap:22px;font-size:8px}
.footer-cols h5{font-family:"Oswald",sans-serif;font-weight:400;font-size:9px;color:var(--white);margin-bottom:6px}
.footer-cols div div{margin-bottom:4px}
.news{position:absolute;left:470px;top:14px;width:185px;height:140px;background:#2d2d2d;border:1px solid #444}
.news h5{font-size:9px;color:#fff;background:#3b3b3b;padding:4px 8px}
.news-item{display:flex;gap:5px;padding:5px 6px;border-bottom:1px solid #444;font-size:7.5px;line-height:1.3}
.news-item i{flex:0 0 22px;height:18px;background:#666}
.news-more{font-size:7.5px;text-align:right;padding:4px 8px;color:#ddd}
.footer-brand{position:absolute;left:676px;top:20px;width:115px;text-align:center}
.footer-brand .circle{width:56px;height:56px;border-radius:50%;background:var(--red);margin:0 auto 6px}
.footer-brand-name{font-family:"Oswald",sans-serif;font-weight:700;font-size:12px;line-height:1.15;color:var(--white);letter-spacing:.5px}
.footer-brand-name small{display:block;font-size:8px;letter-spacing:2px;font-weight:700}
.site-footer .social{position:absolute;left:683px;top:138px}
.footer-bar{position:absolute;bottom:0;left:0;width:851px;height:22px;background:#111;font-size:8px;color:#999}
.footer-bar span{position:absolute;top:6px}
</style>
</head>
<body>

<header class="site-header">
  <div class="brand">
    <div class="brand-mark"></div>
    <div class="brand-name">VANTREX<small>INTERNATIONAL</small></div>
  </div>
  <div class="contact-line">
    <span><svg width="10" height="8" viewBox="0 0 10 8"><rect x=".5" y=".5" width="9" height="7" fill="none" stroke="#ccc"/><path d="M.5 .5 5 4.5 9.5 .5" fill="none" stroke="#ccc"/></svg>info@vantrexintl.com</span>
    <span><svg width="8" height="10" viewBox="0 0 8 10"><rect x=".5" y=".5" width="7" height="9" rx="1.5" fill="none" stroke="#ccc"/></svg>0100 555 0199</span>
  </div>
  <div class="tagline">High Risk Training for Law Enforcement Agencies Worldwide</div>
  <div class="social"><span></span><span></span><span></span><span></span><span></span></div>
</header>

<nav class="main-nav">
  <ul>
    <li>ABOUT US</li>
    <li class="active">SERVICES</li>
    <li>COURSES</li>
    <li>NEWS</li>
    <li>CONTACT US</li>
  </ul>
  <div class="search">Search</div>
</nav>
<div class="dropdown"><div>Training</div><div>Services</div></div>

<section class="hero" role="img" aria-label="Bomb technician in a protective suit approaching a suspect device in a street">
  <div class="hero-arrow prev"><svg width="32" height="32"><path d="M18 10 12 16 18 22" fill="none" stroke="#fff" stroke-width="2.5"/></svg></div>
  <div class="hero-arrow next"><svg width="32" height="32"><path d="M14 10 20 16 14 22" fill="none" stroke="#fff" stroke-width="2.5"/></svg></div>
  <div class="hero-caption">
    <h1>COUNTER I.E.D. TRAINING</h1><br>
    <p>High Level Courses in Identification and Disposal</p>
  </div>
</section>

<div class="band" style="top:488px"><span class="band-dot"></span><h2>WHO WE ARE</h2></div>

<section class="wrap about">
  <h3>Welcome to Vantrex International</h3>
  <p>We deliver High Risk Training to Law Enforcement Agencies throughout the world.</p>
  <p>Our focus is on Improvised Explosive Devices.</p>
  <p>We train Bomb Technicians and First Responders in all aspects relating to bombings and criminal incidents globally.</p>
  <div class="video" role="img" aria-label="Training video still showing instructors and trainees">
    <div class="video-title">Course Training Video</div>
    <div class="play"><svg width="42" height="30"><path d="M17 9 27 15 17 21Z" fill="#fff"/></svg></div>
  </div>
  <div class="watch-btn">Watch Our Video or Click Here for More Detail &#9656;</div>
</section>

<div class="band" style="top:765px"><span class="band-dot"></span><h2>WHAT WE DO</h2></div>

<div class="services-bg"></div>
<div class="cards">
  <div class="card"><div class="card-img" role="img" aria-label="Technicians working on a device outdoors"></div><h4>IED Training</h4></div>
  <div class="card hover"><div class="card-img" role="img" aria-label="Course photo"><div class="card-icons">
    <span><svg width="14" height="14"><path d="M5 9 9 5M3 7l-1 1a2.5 2.5 0 0 0 4 4l1-1M11 7l1-1a2.5 2.5 0 0 0-4-4L7 3" fill="none" stroke="#fff" stroke-width="1.6"/></svg></span>
    <span><svg width="14" height="14"><circle cx="6" cy="6" r="4" fill="none" stroke="#fff" stroke-width="1.6"/><path d="M9 9 13 13" stroke="#fff" stroke-width="1.6"/></svg></span>
  </div></div><h4>IED Training</h4></div>
  <div class="card alt"><div class="card-img" role="img" aria-label="Controlled explosion on a training range"></div><h4>Course 3</h4></div>
  <div class="card"><div class="card-img" role="img" aria-label="Technician in a bomb suit"></div><h4>Course 4</h4></div>
</div>

<footer class="site-footer">
  <div class="footer-cols">
    <div><h5>HOME</h5></div>
    <div><h5>ABOUT US</h5><div>Our Team</div><div>History</div></div>
    <div><h5>SERVICES</h5><div>IED Training</div><div>Course Two</div><div>Course Three</div></div>
    <div><h5>NEWS</h5><div>Updates</div><div>Events</div></div>
    <div><h5>CONTACT</h5><div>Office</div><div>Email Us</div></div>
  </div>
  <div class="news">
    <h5>Latest News</h5>
    <div class="news-item"><i></i><span>New IED course dates announced for spring session</span></div>
    <div class="news-item"><i></i><span>Instructors complete joint exercise with partner agencies</span></div>
    <div class="news-item"><i></i><span>First responder workshop opens for registration now</span></div>
    <div class="news-more">View All News &#9656;</div>
  </div>
  <div class="footer-brand"><div class="circle"></div><div class="footer-brand-name">VANTREX<small>INTERNATIONAL</small></div></div>
  <div class="social"><span></span><span></span><span></span><span></span><span></span></div>
  <div class="footer-bar">
    <span style="left:60px">Copyright &copy; 2015 Vantrex International LLC. All Rights Reserved.</span>
    <span style="right:60px">Sitemap | Privacy Policy | Terms &amp; Conditions</span>
  </div>
</footer>

</body>
</html>
```